Willow Landing - Multifamily Development

Willow Landing is a Luxury Multifamily Development project located in Orange, NJ. This project will be completed in three phases with the first phase about 75% complete. Each phase will have a different name as follows
CEDAR Willow Landing
LANTERN Willow Landing
BRAMBLEWOOD Willow Landing
We are going to install a banner on the side of the first building which will act as advertising for all buildings. We will eventually need advertising that will be in the windows as well as marketing materials . We want the marketing for this project to be similar for all three phases. At the moment, we are starting with this first simple banner. Attached is a rough idea of the look as well as our color palette. If you feel the color palette is a little too monochrome, feel free to propose an accent color. You can also visit our website to see more info on our company as well as the project. www.tarnlv.com Finally, if you need AI files (ie. for the logo), we can send to you. Thanks..

```html
<!DOCTYPE html>
<html lang="en">
<head>
<meta charset="utf-8">
<title>Cedar Willow Landing – Luxury Apartment Rentals</title>
<link href="https://fonts.googleapis.com/css2?family=Antonio:wght@300;400;700&family=Raleway:wght@300;700&display=swap" rel="stylesheet">
<style>
  :root {
    --navy-deep: #3a5273;
    --navy: #405c82;
    --navy-light: #47658e;
    --line-blue: #5b83b8;
    --white: #ffffff;
  }
  html, body {
    margin: 0;
    padding: 0;
    width: 1200px;
    height: 3811px;
    overflow: hidden;
  }
  .banner {
    position: relative;
    width: 1200px;
    height: 3811px;
    background: linear-gradient(160deg, var(--navy-light) 0%, var(--navy) 40%, var(--navy-deep) 65%, var(--navy-light) 100%);
    color: var(--white);
    overflow: hidden;
  }
  .line {
    position: absolute;
    left: 0;
    width: 1200px;
    margin: 0;
    text-align: center;
    line-height: 1;
    white-space: nowrap;
  }
  .brand-name {
    top: 252px;
    font-family: "Antonio", sans-serif;
    font-weight: 700;
    font-size: 275px;
    letter-spacing: 40px;
    padding-left: 40px;
  }
  .brand-sub {
    top: 542px;
    font-family: "Raleway", sans-serif;
    font-weight: 300;
    font-size: 84px;
    letter-spacing: 42px;
    padding-left: 42px;
  }
  .project-name {
    top: 1110px;
    font-family: "Antonio", sans-serif;
    font-weight: 400;
    font-size: 113px;
  }
  .luxury {
    top: 1304px;
    font-family: "Antonio", sans-serif;
    font-weight: 400;
    font-size: 330px;
  }
  .apartment {
    top: 1627px;
    font-family: "Antonio", sans-serif;
    font-weight: 300;
    font-size: 180px;
    letter-spacing: 16px;
    padding-left: 16px;
  }
  .rentals {
    top: 1797px;
    font-family: "Antonio", sans-serif;
    font-weight: 300;
    font-size: 180px;
    letter-spacing: 16px;
    padding-left: 16px;
  }
  .skyline {
    position: absolute;
    top: 2235px;
    left: 0;
    width: 1200px;
    height: 740px;
  }
  .contact {
    font-family: "Raleway", sans-serif;
  }
  .call-label {
    top: 3187px;
    font-size: 104px;
    font-weight: 300;
  }
  .phone {
    top: 3292px;
    font-size: 135px;
    font-weight: 700;
  }
  .visit-label {
    top: 3443px;
    font-size: 74px;
    font-weight: 300;
  }
  .website {
    top: 3562px;
    font-size: 80px;
    font-weight: 300;
  }
  .website strong {
    font-weight: 700;
  }
</style>
</head>
<body>
  <main class="banner">
    <p class="line brand-name">TARN</p>
    <p class="line brand-sub">PROPERTIES</p>

    <h2 class="line project-name">CEDAR WILLOW LANDING</h2>
    <h1 class="line luxury">LUXURY</h1>
    <p class="line apartment">APARTMENT</p>
    <p class="line rentals">RENTALS</p>

    <svg class="skyline" viewBox="0 0 1200 740" xmlns="http://www.w3.org/2000/svg">
      <defs>
        <radialGradient id="skyline-glow" cx="0.5" cy="0.6" r="0.55">
          <stop offset="0" stop-color="#5b83b8" stop-opacity="0.35"/>
          <stop offset="0.7" stop-color="#5b83b8" stop-opacity="0.12"/>
          <stop offset="1" stop-color="#5b83b8" stop-opacity="0"/>
        </radialGradient>
      </defs>
      <rect x="150" y="0" width="900" height="725" fill="url(#skyline-glow)" role="img" aria-label="Line illustration of three apartment towers"/>
      <line x1="0" y1="727" x2="1200" y2="727" stroke="var(--line-blue)" stroke-width="6"/>
    </svg>

    <p class="line contact call-label">CALL NOW</p>
    <p class="line contact phone">973-555-0148</p>
    <p class="line contact visit-label">VISIT US</p>
    <p class="line contact website">website: <strong>www.tarnlv.com</strong></p>
  </main>
</body>
</html>
```